Etiketten für ein Kreativbier
Zielgruppe
Wir sind eine kleine Privatbrauerei und unsere Zielgruppe sind Bierliebhaber.
Aufgabenstellung
Wir erweitern unsere Produktpalette um ein Kreativbier, welches nach Schockolade, Banane und Chili schmeckt. Für unsere klassischen Biersorten haben wir auch klassische Etiketten. Für das neue, ausgefallene Bier, suchen wir auch ein dazupassendes, ausgefallenes Etikett. Das Etikett soll die Grundfarbe weiß haben und die Schrift bzw. Grafik soll in schwarz erfolgen. Der Name vom Bier wird 'WIRAPOMELU' sein - Abkürzung für Walnut Raspberry Melon Bier. Unser Logo soll aber in jedem Fall Bestandteil des Etikettes sein. Im Anhang befindet sich eine Etikette von einem Bier aus unserem Sortiment. Die Größe von dem Etikett muss 1:1 übernommen werden. Auch die Linke Seite mit dem Text und dem Druckfeld, muss identisch bleiben, damit es beim Etikettieren keine Probleme gibt.
Das Textfeld soll im Abschnitt Zutaten folgendermaßen angepasst werden: 'Zutaten: Wasser, Gerstenmalz, Weizenmalz, Hopfen, Hefe, Chili'

```html
<!DOCTYPE html>
<html lang="de">
<head>
<meta charset="utf-8">
<title>HOLMFELD bräu – Wirapomelu Aromabier Etikett</title>
<link rel="stylesheet" href="https://fonts.googleapis.com/css2?family=Roboto+Slab:wght@500;700&family=Lobster&display=swap">
<style>
  :root {
    --backdrop: #f3dc2c;
    --label-white: #f4f5f6;
    --ink: #1f2224;
    --ink-soft: #3a3d40;
    --art-tone: #d9dbdd;
  }
  * { margin: 0; padding: 0; box-sizing: border-box; }
  html, body {
    width: 1200px;
    height: 900px;
    overflow: hidden;
    background: var(--backdrop);
  }
  .canvas {
    position: relative;
    width: 1200px;
    height: 900px;
  }
  .label {
    position: absolute;
    left: 320px;
    top: 100px;
    width: 560px;
    height: 700px;
    background: var(--label-white);
    border-top: 12px solid var(--ink);
    border-bottom: 22px solid var(--ink);
    color: var(--ink);
    text-align: center;
  }
  .label-frame {
    position: absolute;
    inset: 10px 12px;
    border: 2px solid var(--ink-soft);
    pointer-events: none;
  }
  .brand-mark {
    position: absolute;
    left: 50%;
    top: 64px;
    width: 130px;
    height: 130px;
    margin-left: -65px;
    border-radius: 50%;
    background: var(--ink);
  }
  .brand-name {
    position: absolute;
    left: 0;
    right: 0;
    top: 218px;
    font-family: "Roboto Slab", serif;
    font-weight: 700;
    font-size: 42px;
    letter-spacing: 4px;
    line-height: 1.2;
    color: var(--ink);
  }
  .brand-name .brand-sub {
    display: block;
    font-size: 34px;
    letter-spacing: 2px;
    text-transform: lowercase;
  }
  .side-art {
    position: absolute;
    top: 300px;
    width: 120px;
    height: 300px;
    background: linear-gradient(180deg, var(--label-white), var(--art-tone) 50%, var(--label-white));
    border-radius: 40px;
  }
  .side-art--left { left: 22px; }
  .side-art--right { right: 22px; }
  .beer-name {
    position: absolute;
    left: 0;
    right: 0;
    top: 428px;
    font-family: "Lobster", cursive;
    font-size: 66px;
    line-height: 1;
    color: var(--ink);
  }
  .flavour-art {
    position: absolute;
    left: 50%;
    top: 520px;
    width: 92px;
    height: 42px;
    margin-left: -46px;
    border-radius: 21px;
    background: var(--ink-soft);
  }
  .beer-style {
    position: absolute;
    left: 0;
    right: 0;
    top: 586px;
    font-family: "Roboto Slab", serif;
    font-weight: 500;
    font-size: 26px;
    letter-spacing: 4px;
    color: var(--ink);
  }
</style>
</head>
<body>
  <main class="canvas">
    <section class="label" aria-label="Etikett Wirapomelu Aromabier">
      <div class="label-frame"></div>
      <div class="brand-mark"></div>
      <h1 class="brand-name">HOLMFELD<span class="brand-sub">bräu</span></h1>
      <div class="side-art side-art--left" role="img" aria-label="Illustration von Früchten und Blättern, links"></div>
      <div class="side-art side-art--right" role="img" aria-label="Illustration von Früchten und Blättern, rechts"></div>
      <h2 class="beer-name">Wirapomelu</h2>
      <div class="flavour-art" role="img" aria-label="Kleine Illustration einer Zutat"></div>
      <p class="beer-style">AROMABIER</p>
    </section>
  </main>
</body>
</html>
```